Kestrel Facilities Business Card Design

We would now like to design business cards with the new Kestrel Facilities logo

Target Market(s)

Professional

Industry/Entity Type

Professional services

Contact Information for Business Card

Employee name, title, phone number, email address, corporate office address and logo.

Font styles to use
Sans Serif

Colors
0054AA
0677BA
7BADD7
CADEEF
E8F1F8

Requirements
Must have
• My logo
Should not have
• any other pictures or images besides my logo

```html
<!DOCTYPE html>
<html lang="en">
<head>
<meta charset="utf-8">
<title>Kestrel Facilities Business Card</title>
<link rel="stylesheet" href="https://fonts.googleapis.com/css2?family=Rubik:wght@400;500;700&display=swap">
<style>
  :root {
    --brand-deep: #0036c8;
    --brand-blue: #0677e6;
    --brand-mid: #7badd7;
    --brand-pale: #cadeef;
    --brand-mist: #e8f1f8;
    --ink: #4a4a4a;
    --paper: #ffffff;
    --table: #c9c9c9;
  }
  * { box-sizing: border-box; margin: 0; padding: 0; }
  html, body { width: 1200px; height: 800px; overflow: hidden; }
  body {
    background: var(--table);
    font-family: "Rubik", sans-serif;
    position: relative;
  }
  .card {
    position: absolute;
    top: 249px;
    width: 530px;
    height: 303px;
    overflow: hidden;
    box-shadow: 0 10px 28px rgba(0,0,0,0.22);
  }
  .card--front { left: 45px; background: var(--paper); }
  .card--back  { left: 625px; background: var(--brand-blue); }

  /* front */
  .brand-panel {
    position: absolute;
    top: 0; right: 0;
    width: 300px; height: 170px;
    background: var(--brand-blue);
    display: flex; align-items: center; justify-content: center;
  }
  .brand-panel__name {
    color: var(--paper);
    font-weight: 700;
    font-size: 30px;
    letter-spacing: 0.5px;
    text-transform: uppercase;
    text-align: center;
    line-height: 1.15;
  }
  .brand-tint {
    position: absolute;
    top: 170px; right: 80px;
    width: 140px; height: 133px;
    background: var(--brand-pale);
    opacity: 0.85;
  }
  .contact {
    position: absolute;
    left: 34px; bottom: 30px;
  }
  .contact__heading {
    position: relative;
    padding-left: 14px;
    margin-bottom: 14px;
  }
  .contact__heading::before {
    content: "";
    position: absolute;
    left: 0; top: 2px;
    width: 4px; height: 34px;
    background: var(--brand-blue);
  }
  .contact__name {
    color: var(--brand-blue);
    font-weight: 700;
    font-size: 19px;
    text-transform: uppercase;
    letter-spacing: 0.4px;
  }
  .contact__title {
    color: var(--ink);
    font-size: 12px;
    margin-top: 2px;
  }
  .contact__list { list-style: none; padding-left: 14px; }
  .contact__item {
    display: flex; align-items: flex-start; gap: 9px;
    color: var(--ink);
    font-size: 11.5px;
    line-height: 1.35;
    margin-top: 5px;
  }
  .contact__icon { width: 12px; height: 12px; flex: none; margin-top: 2px; }

  /* back */
  .back-brand {
    position: absolute;
    inset: 0;
    display: flex; align-items: center; justify-content: center; gap: 14px;
  }
  .back-brand__mark {
    width: 26px; height: 26px;
    border: 4px solid var(--brand-deep);
  }
  .back-brand__name {
    color: var(--brand-deep);
    font-weight: 700;
    font-size: 34px;
    text-transform: uppercase;
    letter-spacing: 1px;
  }
</style>
</head>
<body>

<section class="card card--front" aria-label="Business card front">
  <div class="brand-panel">
    <p class="brand-panel__name">Kestrel<br>Facilities</p>
  </div>
  <div class="brand-tint" aria-hidden="true"></div>

  <div class="contact">
    <div class="contact__heading">
      <h1 class="contact__name">Daniel Reyes</h1>
      <p class="contact__title">President</p>
    </div>
    <ul class="contact__list">
      <li class="contact__item">
        <svg class="contact__icon" viewBox="0 0 12 12" fill="none" stroke="#0677e6" stroke-width="1.2"><path d="M6 11s4-3.6 4-6.5A4 4 0 0 0 2 4.5C2 7.4 6 11 6 11z"/><circle cx="6" cy="4.6" r="1.4"/></svg>
        <span>412 Harbor View Road<br>Juneau, Alaska 99801</span>
      </li>
      <li class="contact__item">
        <svg class="contact__icon" viewBox="0 0 12 12" fill="none" stroke="#0677e6" stroke-width="1.2"><path d="M2.5 1.5h2l1 2.5-1.3.9a6 6 0 0 0 2.9 2.9l.9-1.3 2.5 1v2a1 1 0 0 1-1 1A8.5 8.5 0 0 1 1.5 2.5a1 1 0 0 1 1-1z"/></svg>
        <span>555-014-2738</span>
      </li>
      <li class="contact__item">
        <svg class="contact__icon" viewBox="0 0 12 12" fill="none" stroke="#0677e6" stroke-width="1.2"><rect x="1" y="2.5" width="10" height="7"/><path d="M1 2.5l5 4 5-4"/></svg>
        <span>info@kestrelfacilities.com</span>
      </li>
      <li class="contact__item">
        <svg class="contact__icon" viewBox="0 0 12 12" fill="none" stroke="#0677e6" stroke-width="1.2"><circle cx="6" cy="6" r="5"/><path d="M1 6h10M6 1c-2 2.6-2 7.4 0 10M6 1c2 2.6 2 7.4 0 10"/></svg>
        <span>kestrelfacilities.com</span>
      </li>
    </ul>
  </div>
</section>

<section class="card card--back" aria-label="Business card back">
  <div class="back-brand">
    <span class="back-brand__mark" aria-hidden="true"></span>
    <p class="back-brand__name">Kestrel Facilities</p>
  </div>
</section>

</body>
</html>
```